Jewelers Website

This is for the DESIGN ONLY.
I am a software programmer and will be doing the development.
New website design for
www.lunacrestgems.com.au
Need a fresh new look for an online only jewellery business who produce their jewellery by hand. I would like it designed in a parallax style. Feel free to recommend fonts to use for the site. This is an Australian based company located in NSW so shots of sites in NSW might make nice background images.
http://vornaplex.me/demo/#theme=parallax
To contain the below sections
About Us
Contact Us
Gallery
Testimonials
Diamond Types
The colour scheme is to be Black / White and Silver.
With the Parallax style there will be moving sections and images for added impact.
Target Market(s)
Young Adults mainly engagement jewellery

```html
<!DOCTYPE html>
<html lang="en">
<head>
<meta charset="utf-8">
<title>Lunacrest Gems</title>
<link href="https://fonts.googleapis.com/css2?family=Arimo:wght@400;700&family=Open+Sans:wght@400;600;700&display=swap" rel="stylesheet">
<style>
:root{
  --black:#000;
  --night:#141414;
  --panel:#1c1c1c;
  --white:#fff;
  --silver:#c9c9c9;
  --orange:#e2621c;
  --green:#1aa54a;
  --blue:#29a9e1;
  --text-dark:#222;
}
*{box-sizing:border-box;margin:0;padding:0}
html,body{width:1200px;height:3152px;overflow:hidden}
body{position:relative;background:var(--black);font-family:"Open Sans",Arial,sans-serif;color:var(--white)}
.abs{position:absolute}
.center-x{transform:translateX(-50%)}
.section{position:absolute;left:0;width:1200px;overflow:hidden}
.photo{position:absolute;inset:0}
.heading{position:absolute;left:0;width:1200px;text-align:center;font-family:"Arimo",Arial,sans-serif;font-weight:400;color:var(--white);text-shadow:0 2px 6px rgba(0,0,0,.45)}
.btn{position:absolute;height:36px;width:160px;border-radius:18px;color:var(--white);font-weight:600;font-size:17px;line-height:36px;text-align:center}
.gem{position:absolute;transform:translate(-50%,-50%) rotate(45deg);border:3px solid var(--white);box-shadow:0 4px 10px rgba(0,0,0,.4)}

/* nav */
.topbar{position:absolute;left:0;top:0;width:1200px;height:99px;background:var(--black);border-bottom:5px solid var(--white);z-index:2}
.nav-link{position:absolute;top:44px;font-size:12.5px;color:var(--white);transform:translateX(-50%)}
.logo{position:absolute;left:601px;top:100px;width:140px;height:140px;transform:translate(-50%,-50%) rotate(45deg);background:linear-gradient(135deg,#3a3a3a,#111);border:2px solid #555;z-index:3}
.logo-name{position:absolute;left:601px;top:100px;transform:translate(-50%,-50%);z-index:4;text-align:center;font-family:"Arimo",Arial,sans-serif;font-size:19px;line-height:23px;color:var(--white);letter-spacing:1px}

/* hero */
.hero{top:99px;height:536px}
.hero-title{top:140px;font-size:58px;line-height:64px;font-weight:700;color:#f2f2f2}
.slider-arrow{position:absolute;top:300px}

/* about */
.about{top:635px;height:483px}
.about-photo{position:absolute;left:189px;top:168px;width:168px;height:159px}
.about-copy{position:absolute;left:382px;top:162px;width:623px;font-size:11.3px;line-height:18px;color:#eee;text-align:justify}
.about-copy p+p{margin-top:10px}

/* gallery */
.gallery{top:1118px;height:612px}
.gallery-sub{position:absolute;top:114px;left:0;width:1200px;text-align:center;font-family:"Arimo",Arial,sans-serif;font-size:27px;text-shadow:0 2px 4px rgba(0,0,0,.5)}

/* testimonials */
.testimonials{top:1730px;height:599px}
.quote{position:absolute;top:168px;width:164px;height:151px;background:var(--white);color:var(--text-dark);font-size:11px;line-height:17px;padding:13px 20px;text-align:justify;border-radius:3px}
.quote::after{content:"";position:absolute;left:50%;bottom:-11px;transform:translateX(-50%);border:11px solid transparent;border-bottom:0;border-top-color:var(--white)}
.avatar{position:absolute;top:344px;width:56px;height:56px;border-radius:50%;border:3px solid var(--white);background:linear-gradient(#cfd6de,#5d6d82)}
.person{position:absolute;top:414px;width:164px;text-align:center}
.person b{display:block;font-size:13px;font-weight:600}
.person span{display:block;font-size:9.5px;color:#ddd}

/* diamond types */
.types{top:2329px;height:441px}
.type-card{position:absolute;top:168px;width:164px;height:197px;border-radius:8px;overflow:hidden;background:var(--black)}
.type-card .thumb{position:absolute;left:0;top:0;width:164px;height:155px}
.type-card .cap{position:absolute;left:0;bottom:0;width:164px;height:42px;line-height:42px;text-align:center;font-size:11.5px}
.cap-light{background:#d6d6d6;color:var(--text-dark)}
.cap-dark{background:var(--black);color:var(--white)}

/* contact */
.contact{top:2770px;height:305px;background:var(--night)}
.field{position:absolute;border:1px solid #bbb;background:#111;color:var(--white);font-size:12px;font-weight:600;padding:6px 12px}

/* footer */
.footer{position:absolute;left:0;top:3075px;width:1200px;height:77px;background:var(--black)}
.copy{position:absolute;left:164px;top:30px;font-size:10.5px;color:#ddd}
.social{position:absolute;top:26px;width:25px;height:25px;border:2px solid var(--white);border-radius:50%}
</style>
</head>
<body>

<header class="topbar">
  <span class="nav-link" style="left:216px">Home</span>
  <span class="nav-link" style="left:305px">About Us</span>
  <span class="nav-link" style="left:420px">Contact Us</span>
  <span class="nav-link" style="left:717px">Gallery</span>
  <span class="nav-link" style="left:828px">Testimonials</span>
  <span class="nav-link" style="left:963px">Diamond Types</span>
</header>
<div class="logo"></div>
<div class="logo-name">LUNACREST<br>GEMS</div>

<section class="section hero">
  <div class="photo" role="img" aria-label="Sunset over a NSW beach with silhouetted headland and anglers" style="background:linear-gradient(180deg,#3d4a66 0%,#8a6a5e 25%,#e08a3a 45%,#f2a040 52%,#6a4a3a 62%,#2a2622 80%,#1a1816 100%)"></div>
  <h1 class="heading hero-title">Exclusive Quality<br>Lunacrest Gems</h1>
  <svg class="slider-arrow" style="left:78px" width="46" height="90" viewBox="0 0 46 90"><path d="M42 3 L5 45 L42 87" fill="none" stroke="#fff" stroke-width="5"/></svg>
  <svg class="slider-arrow" style="left:1078px" width="46" height="90" viewBox="0 0 46 90"><path d="M4 3 L41 45 L4 87" fill="none" stroke="#fff" stroke-width="5"/></svg>
  <div class="gem" role="img" aria-label="Diamond pendant necklace" style="left:320px;top:391px;width:136px;height:136px;background:radial-gradient(#555,#0a0a0a)"></div>
  <div class="gem" role="img" aria-label="Stacked diamond rings" style="left:593px;top:391px;width:136px;height:136px;background:radial-gradient(#666,#0a0a0a)"></div>
  <div class="gem" role="img" aria-label="Loose diamonds" style="left:862px;top:391px;width:136px;height:136px;background:radial-gradient(#5a5a5a,#0a0a0a)"></div>
</section>

<section class="section about">
  <div class="photo" role="img" aria-label="Dark coastal scene with tree silhouettes at dusk" style="background:linear-gradient(180deg,#1e1e1e 0%,#101010 50%,#1a1a1a 100%)"></div>
  <h2 class="heading" style="top:52px;font-size:54px">About Us</h2>
  <div class="about-photo" role="img" aria-label="Model holding a blue gemstone" style="background:linear-gradient(135deg,#2a2a2a,#6b5a4e 45%,#1d3a8a 75%,#0a0a0a)"></div>
  <div class="about-copy">
    <p>At Lunacrest Gems we are passionate about fine jewellery and gems. We feature one of a kind, original and elegant, handmade pieces. Lunacrest Gems handmade jewellery is crafted using exceptional quality metals, integrating designs that are innovative, creative, and unique. After you have consulted with our experienced staff - our highly trained and experienced jewellers hand-make every piece of finely crafted jewellery with a level of care and attention that cannot be matched by machines. Our custom jewellery is Australian-made in our Sydney workshop.</p>
    <p>With our combination of one-to-one customer service, our deep knowledge and experience, we can help you create unique jewellery that cannot be found in any jewellery store. Better still, because we don't waste money on expensive city shop-fronts, we can offer you amazing value on the most beautiful jewellery.</p>
  </div>
  <div class="btn" style="left:527px;top:376px;background:var(--orange)">More Info</div>
</section>

<section class="section gallery">
  <div class="photo" role="img" aria-label="Sunny NSW beach with blue sky, surf and sand" style="background:linear-gradient(180deg,#1f4f9e 0%,#5d8fcf 22%,#b9d3ea 30%,#4e8a6a 36%,#7fc3c9 42%,#d9c9a8 52%,#e2d1ae 100%)"></div>
  <h2 class="heading" style="top:30px;font-size:54px">Gallery</h2>
  <div class="gallery-sub">we specialize in engagement and wedding rings</div>
  <div class="gem" role="img" aria-label="Hand wearing a ring" style="left:269px;top:246px;width:94px;height:94px;background:linear-gradient(135deg,#c98a6a,#4a7aa8)"></div>
  <div class="gem" role="img" aria-label="Diamond cluster" style="left:429px;top:246px;width:94px;height:94px;background:radial-gradient(#999,#222)"></div>
  <div class="gem" role="img" aria-label="Bride portrait" style="left:597px;top:246px;width:94px;height:94px;background:linear-gradient(135deg,#f3e6dc,#b46a4a)"></div>
  <div class="gem" role="img" aria-label="Pair of wedding bands" style="left:761px;top:246px;width:94px;height:94px;background:radial-gradient(#888,#111)"></div>
  <div class="gem" role="img" aria-label="Diamond eternity ring" style="left:931px;top:246px;width:94px;height:94px;background:radial-gradient(#777,#141414)"></div>
  <div class="gem" role="img" aria-label="Yellow diamond" style="left:269px;top:414px;width:94px;height:94px;background:radial-gradient(#e8e0a0,#8a7a40)"></div>
  <div class="gem" role="img" aria-label="Diamond bracelet on blue" style="left:429px;top:414px;width:94px;height:94px;background:radial-gradient(#9aa8c8,#1a2a6a)"></div>
  <div class="gem" role="img" aria-label="Hands with rings" style="left:597px;top:414px;width:94px;height:94px;background:radial-gradient(#bbb,#2a2a2a)"></div>
  <div class="gem" role="img" aria-label="Silver ring close-up" style="left:761px;top:414px;width:94px;height:94px;background:radial-gradient(#eee,#8a8a8a)"></div>
  <div class="gem" role="img" aria-label="Ring on magenta fabric" style="left:931px;top:414px;width:94px;height:94px;background:radial-gradient(#d38ab0,#5a1038)"></div>
  <div class="btn" style="left:527px;top:523px;background:var(--green)">More Info</div>
</section>

<section class="section testimonials">
  <div class="photo" role="img" aria-label="Night view of a coastal town over water" style="background:linear-gradient(180deg,#0e0e0e 0%,#2a2a2a 30%,#3a3a3a 45%,#1e1e1e 70%,#151515 100%)"></div>
  <h2 class="heading" style="top:48px;font-size:54px">Testimonials</h2>
  <svg class="abs" style="left:158px;top:216px" width="20" height="26" viewBox="0 0 20 26"><path d="M16 2 L5 13 L16 24" fill="none" stroke="#fff" stroke-width="4"/></svg>
  <svg class="abs" style="left:1022px;top:216px" width="20" height="26" viewBox="0 0 20 26"><path d="M4 2 L15 13 L4 24" fill="none" stroke="#fff" stroke-width="4"/></svg>

  <div class="quote" style="left:214px">There are many variations of passages of Lorem Ipsum available, but the majority have suffered alteration in some form, by injected humour</div>
  <div class="quote" style="left:412px">There are many variations of passages of Lorem Ipsum available, but the majority have suffered alteration in some form, by injected humour</div>
  <div class="quote" style="left:609px">There are many variations of passages of Lorem Ipsum available, but the majority have suffered alteration in some form, by injected humour</div>
  <div class="quote" style="left:809px">There are many variations of passages of Lorem Ipsum available, but the majority have suffered alteration in some form, by injected humour</div>

  <div class="avatar" role="img" aria-label="Customer photo" style="left:268px"></div>
  <div class="avatar" role="img" aria-label="Customer photo" style="left:466px"></div>
  <div class="avatar" role="img" aria-label="Customer photo" style="left:663px"></div>
  <div class="avatar" role="img" aria-label="Customer photo" style="left:863px;background:linear-gradient(#f0d6d0,#b06a6a)"></div>

  <div class="person" style="left:214px"><b>Lorem Ipsum</b><span>Simply test</span></div>
  <div class="person" style="left:412px"><b>Bonorum et Malorum</b><span>Simply test</span></div>
  <div class="person" style="left:609px"><b>Injected humour</b><span>Simply test</span></div>
  <div class="person" style="left:809px"><b>Embarrassing</b><span>Simply test</span></div>

  <div class="btn" style="left:527px;top:502px;background:var(--blue)">More Info</div>
</section>

<section class="section types">
  <div class="photo" role="img" aria-label="Rocky NSW shoreline under a grey sky" style="background:linear-gradient(180deg,#9aa3ab 0%,#c4c8cc 18%,#7d8890 24%,#a88458 40%,#8a6436 65%,#b89468 100%)"></div>
  <h2 class="heading" style="top:58px;font-size:54px">Diamond Types</h2>
  <div class="type-card" style="left:210px"><div class="thumb" role="img" aria-label="Round brilliant diamonds" style="background:radial-gradient(#aaa,#1a1a1a)"></div><div class="cap cap-light">Bonorum et Malorum</div></div>
  <div class="type-card" style="left:412px"><div class="thumb" role="img" aria-label="Heart cut diamonds" style="background:radial-gradient(#f2f2f2,#8a8a8a)"></div><div class="cap cap-dark">Bonorum et Malorum</div></div>
  <div class="type-card" style="left:612px"><div class="thumb" role="img" aria-label="Scattered diamonds on black" style="background:radial-gradient(#666,#000)"></div><div class="cap cap-light">Bonorum et Malorum</div></div>
  <div class="type-card" style="left:813px"><div class="thumb" role="img" aria-label="Emerald cut diamond ring" style="background:radial-gradient(#fff,#ccc)"></div><div class="cap cap-dark">Bonorum et Malorum</div></div>
</section>

<section class="section contact">
  <h2 class="heading" style="top:38px;font-size:54px">Contact Us</h2>
  <div class="field" style="left:212px;top:134px;width:234px;height:36px">Name</div>
  <div class="field" style="left:475px;top:134px;width:233px;height:36px">Phone</div>
  <div class="field" style="left:742px;top:134px;width:233px;height:36px">Email</div>
  <div class="field" style="left:212px;top:200px;width:496px;height:77px">Message</div>
  <div class="btn" style="left:752px;top:221px;width:158px;background:var(--blue)">More Info</div>
</section>

<footer class="footer">
  <span class="copy">©Copy right 2014 lunacrestgems | All rights reserved.</span>
  <span class="social" style="left:936px"></span>
  <span class="social" style="left:974px"></span>
  <span class="social" style="left:1014px"></span>
</footer>

</body>
</html>
```